Local Flower Farm Needs Business Card Design

I need business cards designed for a flower farm based in Eudora, Kansas.
Business Info:
We are a local cut flower farm located in Eudora, Kansas, founded by Corinne Haldwick. What started as a passion for agriculture and search for more joy in daily life has blossomed into a small business dedicated to providing the community with beautiful, fresh, and sustainable flowers. We specialize in local, seasonal blooms, ensuring that every petal reflects the care and dedication we pour into our craft. Our mission is to deliver the highest quality flowers directly to our customers through local farmers markets and to florists who share our commitment to sustainability. Join us in celebrating the beauty of nature, one bloom at a time!
Contact Details:
Corinne Haldwick
Owner
Phone 913-555-0147
Facebook: Rosalind Thorpe Gardens
Instagram: @RosalindThorpeGardens
Website: RosalindThorpeGardens.example
Target Market(s)
Wholesale to Florists and Direct to Consumer via Farmers Market
Industry/Entity Type
Florist, Farm
Contact Information for Business Card
Name, Contact Info, Logo
Look and feel
Each slider illustrates characteristics of the customer's brand and the style your logo design should communicate.

```html
<!DOCTYPE html>
<html lang="en">
<head>
<meta charset="utf-8">
<title>Rosalind Thorpe Gardens – Business Card</title>
<link href="https://fonts.googleapis.com/css2?family=Cormorant+Garamond:wght@500;600&family=Montserrat:wght@400;500&display=swap" rel="stylesheet">
<style>
  :root {
    --stage: #2c2c2c;
    --teal-deep: #0b242b;
    --teal: #0f3a42;
    --teal-ink: #123a40;
    --paper: #ffffff;
    --mist: #e6e8e8;
    --mist-soft: #f6f7f7;
    --serif: "Cormorant Garamond", "Times New Roman", serif;
    --sans: "Montserrat", Arial, sans-serif;
  }
  * { box-sizing: border-box; margin: 0; padding: 0; }
  html, body { width: 1200px; height: 1015px; overflow: hidden; }
  body {
    background: var(--stage);
    display: flex;
    flex-direction: column;
    align-items: center;
    justify-content: center;
    gap: 56px;
  }
  .card {
    position: relative;
    width: 700px;
    height: 400px;
    overflow: hidden;
    box-shadow: 0 14px 30px rgba(0,0,0,.45);
  }

  /* Front */
  .card--front {
    background: linear-gradient(160deg, var(--teal) 0%, var(--teal-deep) 70%);
  }
  .front__decoration {
    position: absolute;
    right: 40px;
    top: 0;
    width: 300px;
    height: 290px;
    border-radius: 0 0 140px 40px;
    background: radial-gradient(ellipse at 60% 30%, rgba(40,95,104,.45), rgba(15,58,66,0) 70%);
  }
  .front__name {
    position: absolute;
    left: 70px;
    bottom: 60px;
    font-family: var(--serif);
    font-weight: 500;
    font-size: 34px;
    line-height: 1.05;
    letter-spacing: .06em;
    color: var(--paper);
    text-transform: uppercase;
    text-align: center;
  }

  /* Back */
  .card--back { background: var(--paper); }
  .back__tab {
    position: absolute;
    right: 0;
    top: 30px;
    width: 12px;
    height: 40px;
    background: var(--teal);
  }
  .back__decoration {
    position: absolute;
    right: 40px;
    top: 70px;
    width: 260px;
    height: 250px;
    border-radius: 0 0 120px 30px;
    background: linear-gradient(200deg, var(--mist) 0%, var(--mist-soft) 60%, rgba(255,255,255,0) 100%);
  }
  .holder {
    position: absolute;
    right: 40px;
    top: 34px;
    text-align: right;
    color: var(--teal-ink);
  }
  .holder__name {
    font-family: var(--serif);
    font-weight: 600;
    font-size: 30px;
    letter-spacing: .05em;
    text-transform: uppercase;
  }
  .holder__role {
    font-family: var(--sans);
    font-weight: 500;
    font-size: 17px;
  }
  .brand {
    position: absolute;
    left: 40px;
    top: 50px;
    width: 150px;
    height: 150px;
    border: 1.5px solid var(--teal-ink);
    border-radius: 50%;
    display: flex;
    align-items: center;
    justify-content: center;
    text-align: center;
    font-family: var(--serif);
    font-weight: 600;
    font-size: 19px;
    line-height: 1.15;
    letter-spacing: .04em;
    color: var(--teal-ink);
    text-transform: uppercase;
  }
  .contacts {
    position: absolute;
    left: 40px;
    bottom: 34px;
    list-style: none;
    font-family: var(--sans);
    font-size: 20px;
    color: var(--teal-ink);
  }
  .contacts li {
    display: flex;
    align-items: center;
    gap: 10px;
    margin-top: 6px;
  }
  .contacts .icon {
    width: 26px;
    height: 26px;
    flex: none;
  }
</style>
</head>
<body>

  <section class="card card--front">
    <div class="front__decoration" role="img" aria-label="Faint embossed floral monogram decoration"></div>
    <h1 class="front__name">Rosalind Thorpe<br>Gardens</h1>
  </section>

  <section class="card card--back">
    <div class="back__tab"></div>
    <div class="back__decoration" role="img" aria-label="Faint silver floral monogram decoration"></div>

    <div class="holder">
      <p class="holder__name">Corinne Haldwick</p>
      <p class="holder__role">Owner</p>
    </div>

    <div class="brand">Rosalind<br>Thorpe<br>Gardens</div>

    <ul class="contacts">
      <li>
        <svg class="icon" viewBox="0 0 26 26" aria-hidden="true">
          <circle cx="13" cy="13" r="12" fill="none" stroke="#123a40" stroke-width="1.4"/>
          <path d="M9 8.5c.6-.6 1.4-.6 1.8.1l1 1.6c.3.5.2 1-.2 1.4l-.6.5c.6 1.3 1.5 2.2 2.8 2.8l.5-.6c.4-.4.9-.5 1.4-.2l1.6 1c.7.4.7 1.2.1 1.8l-.7.7c-.8.8-2.3.6-4.2-.7-1.9-1.3-3.3-3-4-4.6-.5-1.3-.5-2.3.1-2.9z" fill="#123a40"/>
        </svg>
        913-555-0147
      </li>
      <li>
        <svg class="icon" viewBox="0 0 26 26" aria-hidden="true"><circle cx="13" cy="13" r="12" fill="none" stroke="#123a40" stroke-width="1.4"/></svg>
        Rosalind Thorpe Gardens
      </li>
      <li>
        <svg class="icon" viewBox="0 0 26 26" aria-hidden="true"><circle cx="13" cy="13" r="12" fill="none" stroke="#123a40" stroke-width="1.4"/></svg>
        @RosalindThorpeGardens
      </li>
      <li>
        <svg class="icon" viewBox="0 0 26 26" aria-hidden="true">
          <circle cx="13" cy="13" r="12" fill="none" stroke="#123a40" stroke-width="1.4"/>
          <circle cx="13" cy="13" r="6.5" fill="none" stroke="#123a40" stroke-width="1.2"/>
          <ellipse cx="13" cy="13" rx="2.8" ry="6.5" fill="none" stroke="#123a40" stroke-width="1.1"/>
          <path d="M6.5 13h13M7.5 10h11M7.5 16h11" stroke="#123a40" stroke-width="1"/>
        </svg>
        RosalindThorpeGardens.example
      </li>
    </ul>
  </section>

</body>
</html>
```